New Business Card Design for Manufacturing

We are an engineering/manufacturing company that offers Advanced machining/assembly/engineering services, as well as innovative products for the heavy duty engine cooling markets.

We are looking to get a new business card designed that is clean and modern looking, but still fits the wide range of technical/skilled work we do.

- We hope to use this design as the base for other design work in new Presentations, web, and print work.

Industry/Entity Type

Engineering

Contact Information for Business Card

Our preferred color of blue is (RGB) 22/71/159 but can vary slightly from that color. Our content will be our Logo and full company name (Vantrell Forge Works, Inc.), company address, name, job title, phone number with extension, cell number, fax number, website, and email address on the cards.
We'd like the full company name next to the logo, but we are open to other interpretations of that layout.
Preferably, we would like the back side to be clean with just our logo, and the front to contain all of the contact information.

Colors
2f74b4
0355a3
85abd2

Requirements
Must have
• - Logo, company name, needed content - We are open to interpretation beyond that.
• - Standard size business card.
• - Horizontal orientation.
• - Enough space for lengthy names / job titles (for example, a job title could read "Directory of Human Resources" or "V.P. of Governmental Affairs"). We need this to look clean, whether the title be short (CEO) or long (as described above).

```html
<!DOCTYPE html>
<html lang="en">
<head>
<meta charset="utf-8">
<title>Vantrell Forge Works — Business Card</title>
<link rel="stylesheet" href="https://fonts.googleapis.com/css2?family=Montserrat:wght@400;500;700;800&display=swap">
<style>
  :root {
    --brand-blue: #16479f;
    --deep-blue: #0355a3;
    --mid-blue: #2f74b4;
    --light-blue: #85abd2;
    --ink-grey: #6b6f76;
    --card-white: #ffffff;
    --stage: #2a2c30;
  }
  * { margin: 0; padding: 0; box-sizing: border-box; }
  html, body { width: 1200px; height: 900px; overflow: hidden; }
  body {
    background: var(--stage);
    font-family: "Montserrat", Arial, sans-serif;
    position: relative;
  }
  .card {
    position: absolute;
    width: 600px;
    height: 343px;
    overflow: hidden;
    box-shadow: 0 14px 30px rgba(0,0,0,0.45);
  }
  .card-art { position: absolute; inset: 0; width: 100%; height: 100%; }

  /* Back side */
  .card-back { left: 80px; top: 60px; }
  .back-brand {
    position: absolute;
    left: 48px;
    top: 150px;
    display: flex;
    align-items: center;
    gap: 16px;
  }
  .brand-square {
    width: 34px; height: 34px;
    background: var(--card-white);
  }
  .back-brand-name {
    color: var(--card-white);
    font-weight: 800;
    font-size: 30px;
    line-height: 1.05;
    letter-spacing: 0.5px;
    text-transform: uppercase;
  }

  /* Front side */
  .card-front { left: 520px; top: 480px; background: var(--card-white); }
  .front-brand {
    position: absolute;
    left: 38px; top: 36px;
    display: flex; align-items: center; gap: 12px;
  }
  .front-brand .brand-square { background: var(--brand-blue); width: 28px; height: 28px; }
  .front-brand-name {
    color: var(--brand-blue);
    font-weight: 800;
    font-size: 38px;
    letter-spacing: 1px;
  }
  .person { position: absolute; left: 40px; top: 112px; }
  .person-name {
    color: var(--brand-blue);
    font-weight: 700;
    font-size: 19px;
    letter-spacing: 0.5px;
  }
  .person-title {
    color: var(--ink-grey);
    font-size: 14px;
    margin-top: 2px;
  }
  .contact-list {
    position: absolute;
    left: 40px; top: 176px;
    list-style: none;
  }
  .contact-list li {
    display: flex; align-items: center; gap: 10px;
    height: 23px;
    color: var(--ink-grey);
    font-size: 14px;
  }
  .contact-icon { width: 16px; height: 16px; flex: none; }
  .address {
    position: absolute;
    right: 26px; top: 248px;
    color: var(--ink-grey);
    font-size: 13px;
  }
  .website {
    position: absolute;
    left: 40px; bottom: 6px;
    color: var(--card-white);
    font-size: 13px;
    letter-spacing: 2px;
  }
</style>
</head>
<body>

<section class="card card-back" aria-label="Card back">
  <svg class="card-art" viewBox="0 0 600 343" preserveAspectRatio="none" aria-hidden="true">
    <defs>
      <linearGradient id="backGradient" x1="0" y1="1" x2="1" y2="0">
        <stop offset="0" stop-color="#0b4fa8"/>
        <stop offset="0.55" stop-color="#2f6cbc"/>
        <stop offset="1" stop-color="#85abd2"/>
      </linearGradient>
    </defs>
    <rect width="600" height="343" fill="url(#backGradient)"/>
    <polygon points="0,318 340,318 362,296 600,296 600,343 0,343" fill="#ffffff"/>
    <polygon points="0,324 344,324 366,302 600,302 600,343 0,343" fill="#ffffff"/>
    <polygon points="366,308 600,308 600,343 330,343 350,324" fill="#0355a3"/>
    <polygon points="0,330 330,330 330,343 0,343" fill="#ffffff"/>
  </svg>
  <div class="back-brand">
    <span class="brand-square"></span>
    <div class="back-brand-name">Vantrell<br>Forge Works, Inc.</div>
  </div>
</section>

<section class="card card-front" aria-label="Card front">
  <svg class="card-art" viewBox="0 0 600 343" preserveAspectRatio="none" aria-hidden="true">
    <defs>
      <linearGradient id="frontBand" x1="0" y1="0" x2="1" y2="0">
        <stop offset="0" stop-color="#85abd2"/>
        <stop offset="1" stop-color="#0355a3"/>
      </linearGradient>
    </defs>
    <polyline points="0,308 370,308 392,274 600,274" fill="none" stroke="#16479f" stroke-width="2"/>
    <polygon points="396,280 600,280 600,343 396,343" fill="url(#frontBand)"/>
    <polygon points="0,314 374,314 396,280 396,343 0,343" fill="#16479f"/>
  </svg>

  <div class="front-brand">
    <span class="brand-square"></span>
    <span class="front-brand-name">VANTRELL</span>
  </div>

  <div class="person">
    <div class="person-name">MARCUS HALE</div>
    <div class="person-title">V.P. of Governmental Affairs</div>
  </div>

  <ul class="contact-list">
    <li>
      <svg class="contact-icon" viewBox="0 0 16 16" aria-hidden="true"><circle cx="8" cy="8" r="7" fill="none" stroke="#16479f" stroke-width="1.3"/><path d="M5.3 4.6l1.4 1.5-.7 1a5 5 0 002.9 2.9l1-.7 1.5 1.4-.8 1.1C7.9 11.6 4.4 8.1 4.2 5.4z" fill="#16479f"/></svg>
      (555) 014-2200 x123
    </li>
    <li>
      <svg class="contact-icon" viewBox="0 0 16 16" aria-hidden="true"><circle cx="8" cy="8" r="7" fill="none" stroke="#16479f" stroke-width="1.3"/><rect x="5.6" y="4" width="4.8" height="8" rx="0.8" fill="none" stroke="#16479f" stroke-width="1.2"/></svg>
      555-019-4471
    </li>
    <li>
      <svg class="contact-icon" viewBox="0 0 16 16" aria-hidden="true"><circle cx="8" cy="8" r="7" fill="none" stroke="#16479f" stroke-width="1.3"/><rect x="4.5" y="6.5" width="7" height="4" fill="#16479f"/><rect x="5.8" y="4.2" width="4.4" height="2.3" fill="none" stroke="#16479f" stroke-width="1"/></svg>
      555-016-3385
    </li>
    <li>
      <svg class="contact-icon" viewBox="0 0 16 16" aria-hidden="true"><circle cx="8" cy="8" r="7" fill="none" stroke="#16479f" stroke-width="1.3"/><rect x="4.4" y="5.4" width="7.2" height="5.2" fill="none" stroke="#16479f" stroke-width="1.1"/><path d="M4.4 5.6L8 8.4l3.6-2.8" fill="none" stroke="#16479f" stroke-width="1.1"/></svg>
      marcus@vantrellforge.com
    </li>
  </ul>

  <div class="address">418 Quarry Ln, Dunmore OH 45012</div>
  <div class="website">www.vantrellforge.com</div>
</section>

</body>
</html>
```